Harbourline Electrical Solutions

On one side. LOGO (underneath:) Commercial Industrial Residential

- NAME & CONTACT DETAILS

Marcus T. Hollings
Project Manager

(Cell icon) (441) 555-0187
(Email icon) hlelectricalsolutions@mailvento.com
(Facebook & Instagram icons )@hlelectricalsolutions

Other side: LOGO - underneath ELECTRICAL CONSTRUCTION & MAINTENANCE . LED LIGHTING & AUTOMATION . LIFE SAFETY SYSTEMS (FIRE ALARM / SECURITY) . DATA & COMMUNICATION

```html
<!DOCTYPE html>
<html lang="en">
<head>
<meta charset="utf-8">
<title>Harbourline Electrical Solutions – Business Card</title>
<link href="https://fonts.googleapis.com/css2?family=Lato:wght@400&family=Raleway:wght@500;600;700&display=swap" rel="stylesheet">
<style>
  :root {
    --backdrop: #333333;
    --card-white: #ffffff;
    --brand-teal: #0f5468;
    --text-grey: #3f3f3f;
    --text-white: #ffffff;
  }
  * { margin: 0; padding: 0; box-sizing: border-box; }
  html, body {
    width: 1200px; height: 900px; overflow: hidden;
    background: var(--backdrop);
  }
  .canvas { position: relative; width: 1200px; height: 900px; }

  .card {
    position: absolute; top: 200px;
    width: 310px; height: 502px;
  }
  .card--front {
    left: 253px;
    background: var(--card-white);
    border-radius: 62px 0 62px 0;
  }
  .card--back {
    left: 627px;
    background: var(--brand-teal);
    border-radius: 0 62px 0 62px;
  }

  /* Front */
  .brand-name {
    position: absolute; left: 24px; top: 98px; width: 270px;
    font-family: "Raleway", sans-serif; font-weight: 700;
    color: var(--brand-teal); line-height: 1;
  }
  .brand-name__main { display: block; font-size: 33px; letter-spacing: 0.5px; }
  .brand-name__sub { display: block; font-size: 14.5px; letter-spacing: 1.6px; margin-top: 7px; }
  .tagline {
    position: absolute; left: 24px; top: 165px;
    font-family: "Lato", sans-serif; font-size: 14px;
    color: var(--text-grey); letter-spacing: 0.1px;
  }
  .person { position: absolute; left: 27px; top: 303px; }
  .person__name {
    font-family: "Raleway", sans-serif; font-weight: 700; font-size: 17px;
    color: var(--brand-teal); letter-spacing: 0.4px;
  }
  .person__title {
    font-family: "Lato", sans-serif; font-size: 14px; color: var(--text-grey);
    margin-top: 1px;
  }
  .contacts { position: absolute; left: 24px; top: 356px; list-style: none; }
  .contacts__item {
    display: flex; align-items: center; height: 26px;
    font-family: "Lato", sans-serif; font-size: 14px; color: var(--text-grey);
  }
  .contacts__icon { width: 22px; height: 22px; margin-right: 7px; flex: none; }

  /* Back */
  .back-brand {
    position: absolute; left: 0; top: 160px; width: 100%;
    text-align: center; font-family: "Raleway", sans-serif; font-weight: 700;
    color: var(--text-white); line-height: 1;
  }
  .back-brand__main { display: block; font-size: 38px; letter-spacing: 1px; }
  .back-brand__sub { display: block; font-size: 15px; letter-spacing: 2.4px; margin-top: 10px; }
  .services {
    position: absolute; left: 0; top: 348px; width: 100%;
    list-style: none; text-align: center;
    font-family: "Raleway", sans-serif; font-weight: 600; font-size: 14.5px;
    line-height: 18.2px; color: var(--text-white); letter-spacing: 0.1px;
  }
</style>
</head>
<body>
<div class="canvas">

  <section class="card card--front">
    <div class="brand-name">
      <span class="brand-name__main">HARBOURLINE</span>
      <span class="brand-name__sub">ELECTRICAL SOLUTIONS</span>
    </div>
    <p class="tagline">COMMERCIAL INDUSTRIAL RESIDENTIAL</p>

    <div class="person">
      <p class="person__name">MARCUS T. HOLLINGS</p>
      <p class="person__title">Project Manager</p>
    </div>

    <ul class="contacts">
      <li class="contacts__item">
        <svg class="contacts__icon" viewBox="0 0 22 22" aria-hidden="true">
          <circle cx="11" cy="11" r="10" fill="none" stroke="var(--brand-teal)" stroke-width="1.3"/>
          <rect x="7.5" y="5" width="7" height="12" rx="1.3" fill="none" stroke="var(--text-grey)" stroke-width="1.2"/>
          <line x1="10" y1="15.2" x2="12" y2="15.2" stroke="var(--text-grey)" stroke-width="1"/>
        </svg>
        (441) 555-0187
      </li>
      <li class="contacts__item">
        <svg class="contacts__icon" viewBox="0 0 22 22" aria-hidden="true">
          <circle cx="11" cy="11" r="10" fill="none" stroke="var(--brand-teal)" stroke-width="1.3"/>
          <rect x="6" y="7.5" width="10" height="7" fill="var(--text-grey)"/>
          <polyline points="6,7.5 11,11.5 16,7.5" fill="none" stroke="#fff" stroke-width="1"/>
        </svg>
        hlelectricalsolutions@mailvento.com
      </li>
      <li class="contacts__item">
        <svg class="contacts__icon" viewBox="0 0 22 22" aria-hidden="true">
          <circle cx="11" cy="11" r="10" fill="none" stroke="var(--brand-teal)" stroke-width="1.3"/>
        </svg>
        @hlelectricalsolutions
      </li>
      <li class="contacts__item">
        <svg class="contacts__icon" viewBox="0 0 22 22" aria-hidden="true">
          <circle cx="11" cy="11" r="10" fill="none" stroke="var(--brand-teal)" stroke-width="1.3"/>
        </svg>
        @hlelectricalsolutions
      </li>
    </ul>
  </section>

  <section class="card card--back">
    <div class="back-brand">
      <span class="back-brand__main">HARBOURLINE</span>
      <span class="back-brand__sub">ELECTRICAL SOLUTIONS</span>
    </div>
    <ul class="services">
      <li>ELECTRICAL CONSTRUCTION</li>
      <li>MAINTENANCE</li>
      <li>LED LIGHTING &amp; AUTOMATION</li>
      <li>DATA &amp; COMMUNICATION</li>
      <li>LIFE SAFETY SYSTEMS</li>
      <li>(FIRE ALARM / SECURITY)</li>
    </ul>
  </section>

</div>
</body>
</html>
```